Etiketten-Design für Kaffeetüten
Zielgruppe
Wir stellen eine nachhaltige alternative zu herkömmlichem Bohnenkaffee her.
Regional, nachhaltig und koffeinfrei.
Hierzu verwenden wir Süßlupinen die wir von einem Partnerbauern aus Niedersachsen beziehen. Diese Lupinen werden wie herkömmlicher Kaffee in einem Trommelröster geröstet und anschließend gemahlen.
Unser Lupinenkaffee kann wie herkömmlicher Kaffee im Filter in der Frenchpress oder in einem Espressokocher zubereitet werden.
Wir bieten unseren Kunden zwei verschiedene Sorten an, eine 'Mild' und eine 'Klassisch'.
Die Zielgruppe sind ernährungsbewusste Menschen die gezielt eine alternative zu herkömmlichen Bohnenkaffee suchen. (Koffeinfreier Kaffee, Getreidekaffee)
Aufgabenstellung
Wir möchten ein modernes Design des Etiketts, das den Stil des Logos widerspiegelt. Die beiden Sorten 'Mild' und 'Klassisch' sollten gut von einander zu unterscheiden sein.
Es gibt ein Etikett für die Vorderseite, hier soll die Produktbezeichnung 'Lupinenkaffee' sowie die Mengenangabe '500g' stehen.
Ggf. 3 Icons für mögliche Brühmethoden (Filter, Frenchpress, Espressokocher)
Auf dem Etikett der Rückseite müssen zum einen die Zutaten, die Zubereitung sowie die Nährwertangaben (in TabellenForm) angegeben werden. Sowie ein EAN Code die Herstellerangaben und die Adresse der Homepage.
TREVO KAFFEE – Deine nachhaltige Kaffeealternative
Zutaten: weiße Süßlupinen, geröstet
Zubereitung: Du kannst Deinen Lupinenkaffee mit der French Press, dem klassischen Filter oder dem Espressokocher zubereiten. Für den optimalen Geschmack empfehlen wir 8g Kaffeepulver für 100ml.
Hersteller:
TREVO GmbH
Henrietta-Lenz-Weg 47
40477 Düsseldorf
www.TREVOKAFFEE.de
 Nährwertangaben für 100 ml Kaffee
Energie 12kj - 5 kcal
Fett <0,1g
Davon gesättigt <0,1g
Kohlenhydrate <1,0g
Davon Zucker <0,05g
Eiweiß <1,0g
Salz <0,05g
Die Kaffeetüte, auf die das Etikett geklebt wird, ist in einer braunen Kartonfarbe.
Das Etikett für die Kaffeetüten hat die Maße 7x11.
Das Logo hat die Schriftart 'Cera'. Die verwendete Schriftart sollte möglichst gleich sein, oder gut damit harmonieren.

```html
<!DOCTYPE html>
<html lang="de">
<head>
<meta charset="utf-8">
<title>TREVO KAFFEE – Etiketten Klassisch und Mild</title>
<link rel="stylesheet" href="https://fonts.googleapis.com/css2?family=Jost:wght@300;400&display=swap">
<style>
  :root {
    --canvas-bg: #f4f1ec;
    --label-black: #1e1e1e;
    --accent-classic: #4f98a9;
    --accent-mild: #c39b2b;
    --band-text: #1a1a1a;
  }

  html, body {
    margin: 0;
    padding: 0;
    width: 1200px;
    height: 1200px;
    overflow: hidden;
    background: var(--canvas-bg);
  }

  .canvas {
    position: relative;
    width: 1200px;
    height: 1200px;
    font-family: "Jost", "Helvetica Neue", Arial, sans-serif;
  }

  .label {
    position: absolute;
    top: 254px;
    width: 440px;
    height: 692px;
    display: flex;
    background: var(--label-black);
    box-shadow: 0 6px 18px rgba(0, 0, 0, 0.12);
  }

  .label--classic { left: 120px; --accent: var(--accent-classic); }
  .label--mild    { left: 640px; --accent: var(--accent-mild); }

  .label__band {
    width: 110px;
    height: 100%;
    background: var(--accent);
    display: flex;
    align-items: flex-end;
    justify-content: center;
    padding-bottom: 58px;
    box-sizing: border-box;
  }

  .label__product {
    writing-mode: vertical-rl;
    transform: rotate(180deg);
    font-weight: 300;
    font-size: 54px;
    letter-spacing: 2px;
    line-height: 1;
    color: var(--band-text);
    margin: 0;
  }

  .label__panel {
    position: relative;
    flex: 1;
    color: var(--accent);
    text-align: center;
  }

  .label__brand {
    position: absolute;
    left: 0;
    right: 0;
    top: 340px;
    margin: 0;
    font-weight: 400;
    color: var(--accent);
    line-height: 1;
  }

  .label__brand-main {
    display: block;
    font-size: 58px;
    letter-spacing: 14px;
    padding-left: 14px;
  }

  .label__brand-sub {
    display: block;
    margin-top: 14px;
    font-size: 25px;
    letter-spacing: 7px;
    padding-left: 7px;
  }

  .label__variety {
    position: absolute;
    left: 0;
    right: 0;
    top: 484px;
    margin: 0;
    font-weight: 400;
    font-size: 24px;
    letter-spacing: 0.5px;
  }

  .label__brew-methods {
    position: absolute;
    left: 0;
    right: 0;
    top: 558px;
    display: flex;
    justify-content: center;
    gap: 48px;
  }

  .brew-icon {
    width: 48px;
    height: 52px;
    color: var(--accent);
  }

  .label__weight {
    position: absolute;
    left: 0;
    right: 0;
    top: 636px;
    margin: 0;
    font-weight: 400;
    font-size: 23px;
  }
</style>
</head>
<body>
<main class="canvas">

  <section class="label label--classic" aria-label="Etikett Lupinenkaffee Klassisch">
    <div class="label__band">
      <h2 class="label__product">LUPINENKAFFEE</h2>
    </div>
    <div class="label__panel">
      <p class="label__brand">
        <span class="label__brand-main">TREVO</span>
        <span class="label__brand-sub">KAFFEE</span>
      </p>
      <p class="label__variety">Klassisch</p>
      <div class="label__brew-methods">
        <svg class="brew-icon" viewBox="0 0 48 52" aria-label="French Press" role="img">
          <g fill="none" stroke="currentColor" stroke-width="3" stroke-linejoin="round">
            <line x1="20" y1="4" x2="20" y2="12"/>
            <rect x="15" y="2" width="10" height="3" fill="currentColor"/>
            <path d="M8 12 H32 V46 H8 Z"/>
            <path d="M32 18 H38 Q41 18 41 22 V34 Q41 38 38 38 H32"/>
            <line x1="8" y1="24" x2="32" y2="24"/>
            <line x1="6" y1="48" x2="34" y2="48"/>
          </g>
        </svg>
        <svg class="brew-icon" viewBox="0 0 48 52" aria-label="Handfilter" role="img">
          <g fill="none" stroke="currentColor" stroke-width="3" stroke-linejoin="round">
            <line x1="4" y1="10" x2="44" y2="10"/>
            <path d="M8 10 L20 30 H28 L40 10"/>
            <line x1="14" y1="32" x2="34" y2="32"/>
            <path d="M24 38 Q20 44 24 47 Q28 44 24 38 Z" fill="currentColor"/>
          </g>
        </svg>
        <svg class="brew-icon" viewBox="0 0 48 52" aria-label="Espressokocher" role="img">
          <g fill="none" stroke="currentColor" stroke-width="3" stroke-linejoin="round">
            <path d="M20 3 H28 L27 6 H21 Z" fill="currentColor"/>
            <path d="M12 6 H34 L30 24 H16 Z" fill="currentColor"/>
            <path d="M16 24 H30 L36 48 H10 Z"/>
            <path d="M34 8 H40 V20 L32 22"/>
            <line x1="18" y1="36" x2="28" y2="36"/>
          </g>
        </svg>
      </div>
      <p class="label__weight">500g</p>
    </div>
  </section>

  <section class="label label--mild" aria-label="Etikett Lupinenkaffee Mild">
    <div class="label__band">
      <h2 class="label__product">LUPINENKAFFEE</h2>
    </div>
    <div class="label__panel">
      <p class="label__brand">
        <span class="label__brand-main">TREVO</span>
        <span class="label__brand-sub">KAFFEE</span>
      </p>
      <p class="label__variety">Mild</p>
      <div class="label__brew-methods">
        <svg class="brew-icon" viewBox="0 0 48 52" aria-label="French Press" role="img">
          <g fill="none" stroke="currentColor" stroke-width="3" stroke-linejoin="round">
            <line x1="20" y1="4" x2="20" y2="12"/>
            <rect x="15" y="2" width="10" height="3" fill="currentColor"/>
            <path d="M8 12 H32 V46 H8 Z"/>
            <path d="M32 18 H38 Q41 18 41 22 V34 Q41 38 38 38 H32"/>
            <line x1="8" y1="24" x2="32" y2="24"/>
            <line x1="6" y1="48" x2="34" y2="48"/>
          </g>
        </svg>
        <svg class="brew-icon" viewBox="0 0 48 52" aria-label="Handfilter" role="img">
          <g fill="none" stroke="currentColor" stroke-width="3" stroke-linejoin="round">
            <line x1="4" y1="10" x2="44" y2="10"/>
            <path d="M8 10 L20 30 H28 L40 10"/>
            <line x1="14" y1="32" x2="34" y2="32"/>
            <path d="M24 38 Q20 44 24 47 Q28 44 24 38 Z" fill="currentColor"/>
          </g>
        </svg>
        <svg class="brew-icon" viewBox="0 0 48 52" aria-label="Espressokocher" role="img">
          <g fill="none" stroke="currentColor" stroke-width="3" stroke-linejoin="round">
            <path d="M20 3 H28 L27 6 H21 Z" fill="currentColor"/>
            <path d="M12 6 H34 L30 24 H16 Z" fill="currentColor"/>
            <path d="M16 24 H30 L36 48 H10 Z"/>
            <path d="M34 8 H40 V20 L32 22"/>
            <line x1="18" y1="36" x2="28" y2="36"/>
          </g>
        </svg>
      </div>
      <p class="label__weight">500g</p>
    </div>
  </section>

</main>
</body>
</html>
```